Red Mo's Wine Label Project

We need a new entry level wine label called "Red Mo's" for a range of wines we are developing from inland Australia. Our company is made up of three youngish guys who live hard and love taking the mickey. Red Mo is Red Morrie - the largest and loudest of the three partners (and ideally this label will take the mickey out of him). We've grown the grapes ourselves for this first release which will be a 2012 Pinot Gris. Wine style is dry, young, fresh and contemporary and pitched at the sub AUD $10 retail price point. The package will be flint (clear) claret shape bottle with plain screwcap (colour matched to suit the winning label design).

I've attached a couple of photos of Red Morrie to give you some idea of his presence and persona.

Target Market(s)

Semi educated 25 - 40 year old wine drinkers. Skewed towards females.

Industry/Entity Type

Retail

Requirements
Should not have
• Anything traditional or old fashioned

```html
<!DOCTYPE html>
<html lang="en">
<head>
<meta charset="utf-8">
<title>Red Mo's Pinot Gris 2012 Label</title>
<link href="https://fonts.googleapis.com/css2?family=Montserrat:wght@300;400;600&display=swap" rel="stylesheet">
<style>
  :root {
    --backdrop: #f1f1f1;
    --label-top: #2b292a;
    --label-bottom: #1c1a1b;
    --label-edge: #5d5b5c;
    --brand-pink: #e0195a;
    --ink-white: #ffffff;
  }
  * { margin: 0; padding: 0; box-sizing: border-box; }
  html, body {
    width: 1200px;
    height: 2520px;
    overflow: hidden;
    background: var(--backdrop);
  }
  .canvas {
    position: relative;
    width: 1200px;
    height: 2520px;
    background: var(--backdrop);
  }
  .wine-label {
    position: absolute;
    left: 100px;
    top: 426px;
    width: 1000px;
    height: 1667px;
    background: var(--label-top);
    border: 4px solid var(--label-edge);
    font-family: "Montserrat", sans-serif;
  }
  .brand-name {
    position: absolute;
    left: 0;
    top: 110px;
    width: 100%;
    text-align: center;
    color: var(--brand-pink);
    font-weight: 600;
    font-size: 290px;
    line-height: 0.92;
    letter-spacing: -4px;
    text-transform: uppercase;
  }
  .varietal-panel {
    position: absolute;
    left: 0;
    right: 0;
    top: 808px;
    bottom: 0;
    background: var(--label-bottom);
    color: var(--ink-white);
    text-align: center;
  }
  .varietal {
    margin-top: 72px;
    font-weight: 400;
    font-size: 118px;
    line-height: 1;
    letter-spacing: 2px;
  }
  .alcohol {
    margin-top: 48px;
    font-weight: 400;
    font-size: 92px;
    line-height: 1;
    letter-spacing: 5px;
  }
  .vintage {
    margin-top: 40px;
    font-weight: 300;
    font-size: 360px;
    line-height: 1;
    letter-spacing: 4px;
  }
</style>
</head>
<body>
<main class="canvas">
  <section class="wine-label">
    <h1 class="brand-name">Red<br>Mo</h1>
    <div class="varietal-panel">
      <p class="varietal">PINOT GRIS</p>
      <p class="alcohol">ALKOHOL 12%</p>
      <p class="vintage">2012</p>
    </div>
  </section>
</main>
</body>
</html>
```